product development company BRVEMKO LLC business card

We need a business card design for a company based in Texas called 'BRVEMKO LLC'. Our first product is a illuminated portable ice chest that is called ' Copper Harbor coolers'. Copper harbor coolers is trademarked. I would like to have the copper harbor trademark somewhere on the card as well as the BRVEMKO LLC name.

Target Market(s)

outdoor industry

Industry/Entity Type

Business

Contact Information for Business Card

i would like to have BRVEMKO LLC logo larger than the Copper harbor coolers logo.

Font styles to use
Serif
Sans Serif

```html
<!DOCTYPE html>
<html lang="en">
<head>
<meta charset="utf-8">
<title>BRVEMKO LLC Business Card</title>
<link rel="stylesheet" href="https://fonts.googleapis.com/css2?family=Tinos:wght@400;700&display=swap">
<style>
  :root {
    --brand-blue: #0a6cb8;
    --brand-green: #8dbb3c;
    --ink: #111111;
    --paper: #ffffff;
    --backdrop: #eee6da;
  }
  * { margin: 0; padding: 0; box-sizing: border-box; }
  html, body { width: 1189px; height: 1200px; overflow: hidden; }
  body {
    background: var(--backdrop);
    font-family: "Tinos", "Times New Roman", serif;
    position: relative;
  }
  .card {
    position: absolute;
    left: 324px; top: 127px;
    width: 540px; height: 946px;
    background: var(--paper);
    border-radius: 34px;
    overflow: hidden;
    box-shadow: 0 6px 24px rgba(80, 60, 30, 0.18);
    text-align: center;
  }
  .brand-mark {
    position: absolute;
    left: 192px; top: 93px;
    width: 155px; height: 155px;
    background: var(--brand-blue);
    border: 8px solid var(--brand-green);
    border-radius: 8px;
  }
  .brand-name {
    position: absolute; left: 0; right: 0; top: 270px;
    font-size: 78px; line-height: 1;
    color: var(--brand-blue);
    letter-spacing: 1px;
  }
  .brand-suffix {
    position: absolute; left: 78px; right: 78px; top: 340px;
    display: flex; align-items: center; gap: 22px;
    font-size: 52px; line-height: 1;
    color: var(--brand-green);
  }
  .brand-suffix::before, .brand-suffix::after {
    content: ""; flex: 1; height: 2px; background: var(--brand-green);
  }
  .employee-name {
    position: absolute; left: 0; right: 0; top: 489px;
    font-size: 45px; line-height: 1;
    color: var(--brand-blue);
  }
  .employee-role {
    position: absolute; left: 0; right: 0; top: 528px;
    font-size: 30px; line-height: 1; font-weight: 700;
    color: var(--brand-green);
  }
  .contact {
    position: absolute; left: 0; right: 0; top: 660px;
    font-size: 30px; line-height: 35px;
    color: var(--brand-blue);
    letter-spacing: 0.5px;
  }
  .product-name {
    position: absolute; left: 0; right: 0; top: 778px;
    display: flex; justify-content: center; align-items: center; gap: 12px;
    font-size: 34px; line-height: 1; font-weight: 700;
    color: var(--ink);
  }
  .product-name .mark {
    width: 30px; height: 30px; background: var(--ink);
  }
  .footer-rule {
    position: absolute; left: 0; right: 0; top: 865px;
    height: 6px; background: var(--brand-green);
  }
  .footer-band {
    position: absolute; left: 0; right: 0; top: 871px; bottom: 0;
    background: var(--brand-blue);
    color: var(--paper);
    font-size: 27px; font-weight: 700; letter-spacing: 0.5px;
    display: flex; align-items: center; justify-content: center;
  }
</style>
</head>
<body>
  <main class="card">
    <div class="brand-mark"></div>
    <div class="brand-name">BRVEMKO</div>
    <div class="brand-suffix">LLC</div>

    <div class="employee-name">EMPLOYEE NAME</div>
    <div class="employee-role">Maneger</div>

    <div class="contact">
      <div class="phone">123 456 7890</div>
      <div class="email">your@yourcompany.com</div>
    </div>

    <div class="product-name"><span class="mark"></span>Copper Harbor</div>

    <div class="footer-rule"></div>
    <div class="footer-band">www.yourcompany.com</div>
  </main>
</body>
</html>
```